Design a building access mobile app for Quillo by Tamberlin Entry Systems

Hello, We're looking for an awesome designer to create an app design for our app Quillo, by Tamberlin Entry Systems. the mobile app allows employees open their office doors with their mobile phone. this means they don't have to use those plastic card badges or keys. We like clean modern design, dark and light themes. We don't have a logo yet.
Updates

Reason: Waiting on a couple designers to submit concepts

Target Market(s)

Commercial and employees

Industry/Entity Type

Building

Font styles to use
Sans Serif
Other font styles liked:
• Oswald extra light

Requirements
Must have
• nice clean design

```html
<!DOCTYPE html>
<html lang="en">
<head>
<meta charset="utf-8">
<title>Tamberlin Security – Door Access</title>
<link rel="stylesheet" href="https://fonts.googleapis.com/css2?family=Oswald:wght@200;300;400&family=Inter:wght@400;500&display=swap">
<style>
  :root {
    --teal: #1cb5cf;
    --ocean: #2488bd;
    --deep-blue: #1f5f9f;
    --accent: #5199df;
    --accent-line: #a9c9ec;
    --white: #ffffff;
    --paper: #ffffff;
  }
  * { margin: 0; padding: 0; box-sizing: border-box; }
  html, body { width: 675px; height: 1200px; overflow: hidden; background: var(--paper); }
  .app {
    position: relative;
    width: 675px;
    height: 1200px;
    overflow: hidden;
    background: var(--paper);
    font-family: "Oswald", sans-serif;
  }
  .hero {
    position: absolute;
    left: 0; top: 0;
    width: 675px; height: 567px;
    background: linear-gradient(150deg, var(--teal) 0%, var(--ocean) 55%, var(--deep-blue) 100%);
    color: var(--white);
  }
  .top-bar {
    position: absolute;
    left: 0; top: 0;
    width: 675px; height: 114px;
    background: rgba(255, 255, 255, 0.05);
  }
  .status-bar {
    position: absolute;
    left: 0; top: 0;
    width: 675px; height: 38px;
    font-family: "Inter", sans-serif;
    font-size: 19px;
    color: var(--white);
  }
  .status-bar .carrier { position: absolute; left: 12px; top: 7px; display: flex; align-items: center; gap: 6px; }
  .status-bar .time { position: absolute; left: 0; right: 0; top: 7px; text-align: center; font-weight: 500; }
  .status-bar .power { position: absolute; right: 10px; top: 7px; display: flex; align-items: center; gap: 8px; }
  .menu-button { position: absolute; left: 23px; top: 63px; }
  .app-title {
    position: absolute;
    left: 0; right: 0; top: 52px;
    text-align: center;
    font-weight: 300;
    font-size: 31px;
    letter-spacing: 0;
    line-height: 1;
  }
  .location-pin { position: absolute; left: 291px; top: 194px; }
  .address {
    position: absolute;
    left: 0; right: 0; top: 322px;
    text-align: center;
    font-weight: 300;
    font-size: 51px;
    line-height: 66px;
    letter-spacing: 1.5px;
    font-style: normal;
  }
  .door-control { position: absolute; left: 0; top: 567px; width: 675px; height: 633px; }
  .door-label {
    position: absolute;
    left: 0; right: 0; top: 296px;
    text-align: center;
    font-weight: 400;
    font-size: 31px;
    letter-spacing: 2px;
    color: var(--white);
    line-height: 1;
  }
</style>
</head>
<body>
<main class="app">
  <section class="hero">
    <header class="top-bar">
      <div class="status-bar">
        <div class="carrier">
          <svg width="68" height="14" viewBox="0 0 68 14" aria-hidden="true">
            <circle cx="6" cy="7" r="5.5" fill="#fff"/>
            <circle cx="19" cy="7" r="5.5" fill="#fff"/>
            <circle cx="32" cy="7" r="5.5" fill="#fff"/>
            <circle cx="45" cy="7" r="5" fill="none" stroke="#fff" stroke-width="1.2"/>
            <circle cx="58" cy="7" r="5" fill="none" stroke="#fff" stroke-width="1.2"/>
          </svg>
          <span>Nettlo</span>
          <svg width="22" height="16" viewBox="0 0 22 16" aria-hidden="true">
            <path d="M11 15 L7.5 11 A5 5 0 0 1 14.5 11 Z" fill="#fff"/>
            <path d="M4.5 8 A9.5 9.5 0 0 1 17.5 8" fill="none" stroke="#fff" stroke-width="2.2" stroke-linecap="round"/>
            <path d="M1.5 4.8 A14 14 0 0 1 20.5 4.8" fill="none" stroke="#fff" stroke-width="2.2" stroke-linecap="round"/>
          </svg>
        </div>
        <div class="time">1:23 AM</div>
        <div class="power">
          <svg width="12" height="20" viewBox="0 0 12 20" aria-hidden="true">
            <path d="M1 5 L10 14 L5.5 18.5 V1.5 L10 6 L1 15" fill="none" stroke="rgba(255,255,255,0.6)" stroke-width="1.4"/>
          </svg>
          <span>77%</span>
          <svg width="44" height="18" viewBox="0 0 44 18" aria-hidden="true">
            <rect x="1" y="1" width="38" height="16" rx="3" fill="none" stroke="#fff" stroke-width="1.5"/>
            <rect x="3.5" y="3.5" width="26" height="11" rx="1.5" fill="#fff"/>
            <rect x="40.5" y="6" width="2.5" height="6" rx="1" fill="#fff"/>
          </svg>
        </div>
      </div>
      <svg class="menu-button" width="38" height="26" viewBox="0 0 38 26" aria-label="Menu" role="img">
        <rect x="0" y="0" width="38" height="3" fill="#fff"/>
        <rect x="0" y="11.5" width="38" height="3" fill="#fff"/>
        <rect x="0" y="23" width="38" height="3" fill="#fff"/>
      </svg>
      <h1 class="app-title">TAMBERLIN SECURITY</h1>
    </header>

    <svg class="location-pin" width="94" height="94" viewBox="0 0 94 94" aria-label="Location" role="img">
      <circle cx="47" cy="47" r="47" fill="#fff"/>
      <path d="M47 77 L33 50 A16 16 0 1 1 61 50 Z" fill="var(--accent)"/>
      <circle cx="47" cy="42" r="6.5" fill="#fff"/>
    </svg>

    <address class="address">2286 NE Linden Parkway<br>Bellmont, WA 98021</address>
  </section>

  <section class="door-control">
    <svg width="675" height="633" viewBox="0 0 675 633" aria-hidden="true">
      <line x1="337.5" y1="77" x2="337.5" y2="208" stroke="var(--accent-line)" stroke-width="1"/>
      <line x1="337.5" y1="426" x2="337.5" y2="553" stroke="var(--accent-line)" stroke-width="1"/>
      <circle cx="337.5" cy="317" r="108" fill="none" stroke="var(--accent)" stroke-width="2.6"/>
      <circle cx="337.5" cy="317" r="78" fill="var(--accent)"/>
      <polyline points="120,293 96,317 120,341" fill="none" stroke="var(--accent)" stroke-width="3.5" stroke-linecap="round" stroke-linejoin="round"/>
      <polyline points="555,293 579,317 555,341" fill="none" stroke="var(--accent)" stroke-width="3.5" stroke-linecap="round" stroke-linejoin="round"/>
    </svg>
    <div class="door-label">DOOR</div>
  </section>
</main>
</body>
</html>
```